Upscale business cards needed for Board of Directors

We need professional business cards created for members of our family business Board of Directors. We would like these relatively simple and straightforward, but also with a unique element to set them apart. Probably stick with neutral and simple colors - white, grey etc. We need space for the traditional elements, including name, title, address, email/phone number. And we will be creating several from this template so it needs to be template that is easy to switch information in and out of.
Business
See description

```html
<!DOCTYPE html>
<html lang="en">
<head>
<meta charset="utf-8">
<title>Calder Holdings – Business Card</title>
<link href="https://fonts.googleapis.com/css2?family=Open+Sans:wght@400;700&display=swap" rel="stylesheet">
<style>
  :root {
    --page-bg: #ffffff;
    --card-light: #ffffff;
    --card-dark: #2b2826;
    --accent-gold: #b59b6b;
    --text-light: #ffffff;
    --text-dark: #2b2826;
    --edge: #d9d9d9;
  }
  * { margin: 0; padding: 0; box-sizing: border-box; }
  html, body {
    width: 1200px;
    height: 832px;
    overflow: hidden;
    background: var(--page-bg);
    font-family: "Open Sans", Arial, sans-serif;
  }
  .business-card {
    position: absolute;
    left: 225px;
    top: 175px;
    width: 808px;
    height: 449px;
    display: flex;
    border: 1px solid var(--edge);
  }
  .brand-side {
    width: 326px;
    background: var(--card-light);
    display: flex;
    flex-direction: column;
    align-items: center;
    justify-content: center;
  }
  .brand-name {
    color: var(--text-dark);
    font-weight: 700;
    font-size: 32px;
    line-height: 1.15;
    letter-spacing: 3px;
    text-align: center;
  }
  .divider-dark { width: 7px; background: var(--card-dark); }
  .divider-gold { width: 7px; background: var(--accent-gold); }
  .contact-side {
    flex: 1;
    background: var(--card-dark);
    color: var(--text-light);
    position: relative;
  }
  .holder {
    position: absolute;
    top: 64px;
    left: 0;
    right: 0;
    text-align: center;
  }
  .holder-name {
    font-weight: 700;
    font-size: 24px;
    letter-spacing: 0.5px;
    line-height: 1.3;
  }
  .holder-position {
    font-weight: 400;
    font-size: 21px;
    line-height: 1.3;
  }
  .contact-list {
    position: absolute;
    left: 83px;
    top: 162px;
    list-style: none;
  }
  .contact-item {
    display: flex;
    align-items: center;
    height: 40px;
    font-size: 24px;
    font-weight: 400;
  }
  .contact-icon {
    width: 18px;
    height: 22px;
    margin-right: 20px;
    flex-shrink: 0;
  }
</style>
</head>
<body>
  <article class="business-card">
    <section class="brand-side">
      <div class="brand-name">CALDER<br>HOLDINGS</div>
    </section>
    <div class="divider-dark"></div>
    <div class="divider-gold"></div>
    <section class="contact-side">
      <header class="holder">
        <h1 class="holder-name">NAME SURNAME</h1>
        <p class="holder-position">Position</p>
      </header>
      <ul class="contact-list">
        <li class="contact-item">
          <svg class="contact-icon" viewBox="0 0 18 22" aria-hidden="true">
            <path d="M4 2 L7 2 L8 7 L6 8.5 C7 12 9 14.5 11.5 16 L13 14 L17 16 L16 20 C9 20 2 12 2 4 Z" fill="none" stroke="#b59b6b" stroke-width="1.6" stroke-linejoin="round"/>
          </svg>
          <span>012 345 67890</span>
        </li>
        <li class="contact-item">
          <svg class="contact-icon" viewBox="0 0 18 22" aria-hidden="true">
            <rect x="3" y="3" width="12" height="17" rx="1.5" fill="none" stroke="#b59b6b" stroke-width="1.6"/>
            <line x1="7" y1="17" x2="11" y2="17" stroke="#b59b6b" stroke-width="1.4"/>
          </svg>
          <span>012 345 67891</span>
        </li>
        <li class="contact-item">
          <svg class="contact-icon" viewBox="0 0 18 22" aria-hidden="true">
            <rect x="1.5" y="6" width="15" height="10" fill="none" stroke="#b59b6b" stroke-width="1.5"/>
            <polyline points="1.5,6 9,12 16.5,6" fill="none" stroke="#b59b6b" stroke-width="1.5"/>
          </svg>
          <span>info@company.com</span>
        </li>
        <li class="contact-item">
          <svg class="contact-icon" viewBox="0 0 18 22" aria-hidden="true">
            <circle cx="9" cy="11" r="7" fill="none" stroke="#b59b6b" stroke-width="1.5"/>
            <ellipse cx="9" cy="11" rx="3" ry="7" fill="none" stroke="#b59b6b" stroke-width="1.2"/>
            <line x1="2" y1="11" x2="16" y2="11" stroke="#b59b6b" stroke-width="1.2"/>
          </svg>
          <span>www.company.com</span>
        </li>
        <li class="contact-item">
          <svg class="contact-icon" viewBox="0 0 18 22" aria-hidden="true">
            <path d="M9 21 C5 15 3 11.5 3 8 A6 6 0 0 1 15 8 C15 11.5 13 15 9 21 Z" fill="#b59b6b"/>
            <circle cx="9" cy="8" r="2.4" fill="#2b2826"/>
          </svg>
          <span>Address</span>
        </li>
      </ul>
    </section>
  </article>
</body>
</html>
```